Book Cover Design - Business/Self-Help Book

Book cover design for a business/self-help book. The title of the book is "COMET Mindset - The Complete Blueprint of Victory" It should also have "Build the Nine Quiet Habits Behind Lasting Growth" as a subtitle somewhere.

Please see the website for an idea of the logo and sub-words: http://www.cometmindset.net

Book size will be 8.5" x 5.25"
Author info: Dalton Pruett

If your design includes a shark on the cover, it MUST be a hammerhead shark. Logo is attached.

I would like to stick with a red or orange theme like on the website but am open to any color idea. I like brighter colors and want the book to stand out and be attractive. If it's white, the wording and logo should be a bright color.

The back cover will just be preview text and selling points. It could have a picture in the background but will not have any pictures of the author.

If you include a spine design, please put the hammerhead logo on the spine.
Updates

Target Market(s)

Young Entrepreneurs and Business Professionals

Industry/Entity Type

Business

Requirements
Must have
• The hammerhead shark logo
Nice to have
• Look at the website - http://www.cometmindset.net
• It would be nice to have the six words throughout the cover similar to how it shows on the website cover picture.
Should not have
• Even though it caters to a younger crowd, it should not be cartoonish or child-like. Want a more serious and modern feel. Not too cluttered, i want the title to stand out and the shark to stand out.

```html
<!DOCTYPE html>
<html lang="en">
<head>
<meta charset="utf-8">
<title>COMET Mindset – Book Cover</title>
<link rel="stylesheet" href="https://fonts.googleapis.com/css2?family=League+Spartan:wght@700;800&family=Quando&display=swap">
<style>
  :root {
    --stage: #e4e9ee;
    --cover: #252525;
    --accent: #ee9638;
    --ink-light: #ffffff;
    --photo-dark: #3a3a3a;
    --photo-mid: #6b6b6b;
    --photo-light: #a9a9a9;
  }
  html, body {
    margin: 0;
    padding: 0;
    width: 1200px;
    height: 901px;
    overflow: hidden;
    background: var(--stage);
  }
  .stage {
    position: relative;
    width: 1200px;
    height: 901px;
  }
  .cover {
    position: absolute;
    left: 321px;
    top: 0;
    width: 557px;
    height: 901px;
    background: var(--cover);
    box-shadow: 0 6px 24px rgba(0,0,0,0.18);
    overflow: hidden;
  }
  .title-block {
    position: absolute;
    left: 40px;
    top: 52px;
    width: 474px;
    height: 340px;
  }
  .title-block text {
    font-family: "League Spartan", "Arial Black", sans-serif;
    font-weight: 800;
    fill: var(--accent);
  }
  .subtitle {
    position: absolute;
    left: 40px;
    width: 474px;
    top: 404px;
    margin: 0;
    font-family: "League Spartan", Arial, sans-serif;
    font-weight: 700;
    font-size: 15.5px;
    color: var(--ink-light);
    text-align: center;
    white-space: nowrap;
  }
  .hero-photo {
    position: absolute;
    left: 40px;
    top: 452px;
    width: 480px;
    height: 370px;
    border-radius: 46% 38% 42% 30% / 40% 44% 36% 48%;
    background: radial-gradient(ellipse at 55% 40%, var(--photo-light) 0%, var(--photo-mid) 45%, var(--photo-dark) 100%);
  }
  .author {
    position: absolute;
    left: 0;
    width: 557px;
    top: 822px;
    margin: 0;
    font-family: "Quando", Georgia, serif;
    font-size: 26px;
    color: var(--ink-light);
    text-align: center;
  }
</style>
</head>
<body>
<main class="stage">
  <section class="cover" aria-label="Book cover: COMET Mindset">
    <svg class="title-block" viewBox="0 0 474 340" aria-label="COMET Mindset – The Complete Blueprint of Victory">
      <text class="title-main" x="0" y="108" font-size="128" textLength="474" lengthAdjust="spacingAndGlyphs">COMET</text>
      <text class="title-main" x="0" y="226" font-size="128" textLength="474" lengthAdjust="spacingAndGlyphs">MINDSET</text>
      <text class="title-tag" x="0" y="272" font-size="40" textLength="474" lengthAdjust="spacingAndGlyphs">THE COMPLETE BLUEPRINT</text>
      <text class="title-tag" x="0" y="328" font-size="64" textLength="474" lengthAdjust="spacingAndGlyphs">OF VICTORY</text>
    </svg>
    <p class="subtitle">Build the Nine Quiet Habits Behind Lasting Growth</p>
    <div class="hero-photo" role="img" aria-label="Black and white photograph of a hammerhead shark with a grey cut-out outline"></div>
    <p class="author">Dalton Pruett</p>
  </section>
</main>
</body>
</html>
```